Fernhale Business Card Design

We are looking for a fresh business card design for our new logo. We would like a business card that is unique but friendly. We are in the window coverings business offering blinds, shutters and shades for homes.

Target Market(s)

Targeting the end-consumer

Industry/Entity Type

Business

Requirements
Must have
• Must have a dedicates space for a photo of our sales person. Must contain our new logo (attached).

```html
<!DOCTYPE html>
<html lang="en">
<head>
<meta charset="utf-8">
<title>Fernhale Business Card</title>
<link rel="stylesheet" href="https://fonts.googleapis.com/css2?family=Poppins:wght@400;500;600&display=swap">
<style>
  :root {
    --backdrop: #3a3431;
    --leaf: #8bc441;
    --paper: #ffffff;
    --ink: #5a5a5a;
    --slate: #5e5f66;
    --photo-light: #ece8e4;
    --photo-mid: #8a8580;
    --photo-dark: #3b3a39;
  }
  * { box-sizing: border-box; margin: 0; padding: 0; }
  html, body { width: 1200px; height: 930px; overflow: hidden; }
  body {
    background: var(--backdrop);
    font-family: "Poppins", Arial, sans-serif;
    position: relative;
  }
  .card {
    position: absolute;
    width: 580px;
    height: 330px;
    box-shadow: 0 10px 24px rgba(0,0,0,.35);
    overflow: hidden;
  }
  /* front */
  .card-front {
    left: 70px; top: 110px;
    background: var(--leaf);
    color: var(--paper);
  }
  .brand {
    position: absolute;
    left: 0; right: 0; top: 118px;
    display: flex; align-items: center; justify-content: center;
    gap: 18px;
  }
  .brand-mark {
    width: 62px; height: 62px;
    border: 4px solid var(--paper);
    border-radius: 10px;
  }
  .brand-name {
    font-size: 58px;
    font-weight: 500;
    letter-spacing: 1px;
    line-height: 1;
  }
  .front-web {
    position: absolute;
    left: 0; right: 0; bottom: 34px;
    text-align: center;
    font-size: 13px;
    letter-spacing: 1px;
  }
  /* back */
  .card-back {
    left: 550px; top: 490px;
    background: var(--paper);
  }
  .photo {
    position: absolute;
    left: 0; top: 40px;
    width: 300px; height: 290px;
    background: linear-gradient(180deg, var(--paper) 0%, var(--photo-light) 30%, var(--photo-mid) 50%, var(--photo-dark) 65%, var(--photo-dark) 100%);
  }
  .details {
    position: absolute;
    left: 318px; top: 32px;
    width: 250px;
    color: var(--ink);
  }
  .person-name {
    color: var(--leaf);
    font-size: 23px;
    font-weight: 600;
    letter-spacing: 1px;
    line-height: 1.2;
    text-transform: uppercase;
  }
  .person-title {
    font-size: 12px;
    text-transform: uppercase;
    letter-spacing: .5px;
    margin-left: 12px;
  }
  .rule {
    width: 42px; height: 2px;
    background: var(--leaf);
    margin: 16px 0 14px 22px;
  }
  .rule-second { margin-left: 40px; }
  .address {
    font-size: 12.5px;
    line-height: 1.4;
    margin-left: 34px;
  }
  .contacts {
    list-style: none;
    margin-left: 44px;
    font-size: 12.5px;
    line-height: 1.5;
  }
  .contacts li { display: flex; align-items: center; gap: 9px; white-space: nowrap; }
  .contacts svg { width: 11px; height: 11px; fill: var(--leaf); flex: none; }
  .band-leaf {
    position: absolute; left: 300px; bottom: 0;
    width: 130px; height: 14px; background: var(--leaf);
  }
  .band-slate {
    position: absolute; left: 430px; bottom: 0;
    width: 150px; height: 14px; background: var(--slate);
  }
</style>
</head>
<body>
  <section class="card card-front">
    <div class="brand">
      <span class="brand-mark"></span>
      <span class="brand-name">Fernhale</span>
    </div>
    <p class="front-web">www.fernhaleliving.com</p>
  </section>

  <section class="card card-back">
    <div class="photo" role="img" aria-label="Portrait photo of the sales person"></div>
    <div class="details">
      <h1 class="person-name">Dana Whitlow</h1>
      <p class="person-title">Realtor</p>
      <div class="rule"></div>
      <p class="address">P.O.Box: 214,<br>Lakeview, Oregon</p>
      <div class="rule rule-second"></div>
      <ul class="contacts">
        <li><svg viewBox="0 0 12 12"><path d="M2 1h3l1 3-2 1c1 2 2 3 3 3l1-2 3 1v3c-6 0-9-3-9-9z"/></svg>(555) 218-4470</li>
        <li><svg viewBox="0 0 12 12"><path d="M3 0h6v12H3zM4 1v9h4V1z"/></svg>(555) 218-4470</li>
        <li><svg viewBox="0 0 12 12"><path d="M3 0h6v3H3zM1 4h10v5H9v3H3V9H1zM4 8v3h4V8z"/></svg>(555) 218-4470</li>
        <li><svg viewBox="0 0 12 12"><path d="M0 2h12v8H0zM1 3l5 4 5-4z"/></svg>info@fernhalehome.com</li>
        <li><svg viewBox="0 0 12 12"><circle cx="6" cy="6" r="6"/></svg>www.fernhalehome.com</li>
      </ul>
    </div>
    <div class="band-leaf"></div>
    <div class="band-slate"></div>
  </section>
</body>
</html>
```